specialised legal consultancy business needs an update on logo and office stationary.

Update on Logo - see attached.

update on email signature - something new and fresh with only the following details -

(the logo)
Advocate Pieter Vosloo
PV Entity Frameworks (Pty) Ltd (Reg No.: 2019 / 352917 / 07)
LLB, LLM (Cum Laude), Cert.Dir (BFNTA), FCG (PRWEK)
+27 61 552 9047
pieter#vosloolegal.com

Update on letterhead - something new and fresh and please more user-friendly. With the same details as per the email signature.

```html
<!DOCTYPE html>
<html lang="en">
<head>
<meta charset="utf-8">
<title>Vosloo Counsel – Letterhead</title>
<link href="https://fonts.googleapis.com/css2?family=Poppins:wght@400;500;600;700&family=Open+Sans:wght@400&display=swap" rel="stylesheet">
<style>
  :root {
    --bg: #e4e4e4;
    --paper: #ffffff;
    --ink: #111111;
    --body: #3a3a3a;
    --muted: #6b6b6b;
    --rule: #1a1a1a;
    --sig-fill: #ececec;
  }
  html, body {
    margin: 0;
    padding: 0;
    width: 1200px;
    height: 1200px;
    overflow: hidden;
    background: var(--bg);
  }
  .letterhead {
    position: absolute;
    left: 224px;
    top: 68px;
    width: 753px;
    height: 1064px;
    background: var(--paper);
    font-family: "Poppins", sans-serif;
    color: var(--ink);
  }
  .brand-mark {
    position: absolute;
    left: 66px;
    top: 62px;
    width: 78px;
    height: 78px;
    background: var(--ink);
  }
  .brand-divider {
    position: absolute;
    left: 192px;
    top: 60px;
    width: 1.5px;
    height: 72px;
    background: var(--ink);
  }
  .brand-name {
    position: absolute;
    left: 210px;
    top: 75px;
    margin: 0;
    font-size: 17px;
    font-weight: 600;
    letter-spacing: 1.6px;
    line-height: 1;
  }
  .brand-tagline {
    position: absolute;
    left: 222px;
    top: 101px;
    margin: 0;
    font-size: 7.5px;
    letter-spacing: 3.6px;
    color: var(--ink);
    line-height: 1;
  }
  .salutation {
    position: absolute;
    left: 54px;
    top: 287px;
    margin: 0;
    font-size: 15px;
    font-weight: 600;
    line-height: 1.2;
  }
  .letter-body {
    position: absolute;
    left: 51px;
    top: 345px;
    width: 660px;
    font-family: "Open Sans", sans-serif;
    font-size: 12.6px;
    line-height: 15.2px;
    color: var(--body);
  }
  .letter-body p { margin: 0 0 15.2px; }
  .signature {
    position: absolute;
    left: 51px;
    top: 790px;
    width: 160px;
    height: 50px;
    background: var(--sig-fill);
  }
  .role-tab {
    position: absolute;
    left: 54px;
    top: 948px;
    width: 23px;
    height: 116px;
    background: var(--ink);
  }
  .role-tab span {
    position: absolute;
    left: 50%;
    top: 50%;
    transform: translate(-50%, -50%) rotate(-90deg);
    color: var(--paper);
    font-size: 10.5px;
    font-weight: 500;
    letter-spacing: 2px;
    white-space: nowrap;
  }
  .signatory-name {
    position: absolute;
    left: 90px;
    top: 945px;
    margin: 0;
    font-size: 19px;
    font-weight: 600;
    letter-spacing: 0.4px;
    line-height: 1.2;
  }
  .contact-block {
    position: absolute;
    top: 975px;
    margin: 0;
    font-size: 10.3px;
    line-height: 15px;
    color: var(--muted);
  }
  .credentials { left: 90px; }
  .phone-email { left: 446px; }
  .address { left: 605px; }
  .footer-rule {
    position: absolute;
    left: 77px;
    right: 0;
    top: 1012px;
    height: 1.5px;
    background: var(--rule);
  }
  .memberships {
    position: absolute;
    left: 90px;
    top: 1022px;
    margin: 0;
    font-size: 8.4px;
    font-weight: 500;
    color: #2a2a2a;
    white-space: nowrap;
  }
</style>
</head>
<body>
  <main class="letterhead">
    <header>
      <div class="brand-mark"></div>
      <div class="brand-divider"></div>
      <h1 class="brand-name">VOSLOO COUNSEL</h1>
      <p class="brand-tagline">LEGAL CONSULTANCY</p>
    </header>

    <h2 class="salutation">To whom it may concern</h2>

    <section class="letter-body">
      <p>Lorem ipsum dolor sit amet, consectetuer adipiscing elit, sed diam nonummy nibh euismod tincidunt ut laoreet dolore magna aliquam erat volutpat. Ut wisi enim ad minim veniam, quis nostrud exerci tation ullam&shy;corper suscipit lobortis nisl ut aliquip ex ea commodo consequat. Duis autem vel eum iriure dolor in hendre&shy;rit in vulputate velit esse molestie consequat, vel illum dolore eu feugiat nulla facilisis at vero eros et accumsan et iusto odio dignissim qui blandit praesent luptatum zzril delenit augue duis dolore te feugait nulla facilisi.</p>
      <p>Lorem ipsum dolor sit amet, cons ectetuer adipiscing elit, sed diam nonummy nibh euismod tincidunt ut laoreet dolore magna aliquam erat volutpat. Ut wisi enim ad minim veniam, quis nostrud exerci tation ullam&shy;corper suscipit lobortis nisl ut aliquip ex ea commodo consequat.</p>
      <p>Lorem ipsum dolor sit amet, consectetuer adipiscing elit, sed diam nonummy nibh euismod tincidunt ut laoreet dolore magna aliquam erat volutpat. Ut wisi enim ad minim veniam, quis nostrud exerci tation ullam&shy;corper suscipit lobortis nisl ut aliquip ex ea commodo consequat. Duis autem vel eum iriure dolor in hendre&shy;rit in vulputate velit esse molestie consequat, vel illum dolore eu feugiat nulla facilisis at vero eros et accumsan et iusto odio dignissim qui blandit praesent luptatum zzril delenit augue duis dolore te feugait nulla facilisi.</p>
      <p>Lorem ipsum dolor sit amet, cons ectetuer adipiscing elit, sed diam nonummy nibh euismod tincidunt ut laoreet dolore magna aliquam erat volutpat. Ut wisi enim ad minim veniam, quis nostrud exerci tation ullam&shy;corper suscipit lobortis nisl ut aliquip ex ea commodo consequat.</p>
    </section>

    <div class="signature" role="img" aria-label="Handwritten signature"></div>

    <footer>
      <div class="role-tab"><span>ADVOCATE</span></div>
      <h3 class="signatory-name">Pieter Vosloo</h3>
      <p class="contact-block credentials">PV Entity Frameworks (Pty) Ltd (Reg No.: 2019 / 352917 / 07)<br>LLB, LLM (Cum Laude), Cert.Dir (BFNTA), FCG (PRWEK)</p>
      <p class="contact-block phone-email">+27 61 552 9047<br>pieter@vosloolegal.com</p>
      <p class="contact-block address">214 Jacaranda Lane,<br>Waterkloof Heights, Pretoria</p>
      <div class="footer-rule"></div>
      <p class="memberships">Advocate of High Court &nbsp;|&nbsp; Mediator &nbsp;|&nbsp; Chartered Secretary (PRWEK) Nov, 2021 &nbsp;|&nbsp; Member of Southern Legal Advisers Guild</p>
    </footer>
  </main>
</body>
</html>
```